Business Card Design

Online clothing womens clothing store, I sell my clothing online and at the markets.

i would like the attached picture on the front of the card and the contact information on the back.

Industry/Entity Type

Business

Contact Information for Business Card

Marlow Thread
Karen Whitfield
(Instagram symbol) _marlow_thread_
(Facebook symbol) www.fakebookexample.com/marlowthreadau/

W : www.marlowthread.example.au
E : info@marlowthread.example.au
P : 0498716204

```html
<!DOCTYPE html>
<html lang="en">
<head>
<meta charset="UTF-8">
<title>Marlow Thread – Business Card</title>
<link href="https://fonts.googleapis.com/css2?family=Josefin+Sans:wght@300&family=Open+Sans:wght@400;700&family=Oswald:wght@500&display=swap" rel="stylesheet">
<style>
  :root {
    --canvas: #e9e6e1;
    --card-white: #f4f4f3;
    --ink: #2b2b2b;
    --band-black: #2a2a2a;
    --band-orange: #f0a51f;
    --band-orange-deep: #e08e12;
    --photo-light: #d9dadd;
    --photo-mid: #9b98a8;
    --photo-dark: #5c586b;
    --photo-teal: #8fb3b5;
    --text-light: #f2f2f2;
  }
  * { margin: 0; padding: 0; box-sizing: border-box; }
  html, body { width: 1200px; height: 902px; overflow: hidden; }
  body {
    background: var(--canvas);
    position: relative;
    font-family: "Open Sans", sans-serif;
    color: var(--ink);
  }
  .card {
    position: absolute;
    left: 250px;
    width: 700px;
    height: 400px;
    overflow: hidden;
    box-shadow: 0 6px 18px rgba(0,0,0,0.18);
  }
  .card--front { top: 30px; }
  .card--back { top: 472px; background: var(--card-white); }

  /* Front */
  .front-photo {
    position: absolute;
    left: 0; top: 0;
    width: 100%; height: 250px;
    background:
      radial-gradient(ellipse 40% 55% at 62% 35%, var(--photo-dark), transparent 70%),
      radial-gradient(ellipse 30% 40% at 45% 65%, var(--photo-teal), transparent 75%),
      linear-gradient(100deg, var(--photo-light) 0%, var(--photo-light) 30%, var(--photo-mid) 60%, var(--photo-light) 100%);
  }
  .front-name {
    position: absolute;
    left: 28px; top: 150px;
    font-family: "Oswald", sans-serif;
    font-weight: 500;
    font-size: 82px;
    line-height: 1;
    letter-spacing: 2px;
    color: var(--text-light);
    text-transform: uppercase;
    white-space: nowrap;
  }
  .band-orange {
    position: absolute;
    left: 0; width: 100%;
    background: linear-gradient(180deg, var(--band-orange), var(--band-orange-deep));
  }
  .band-black {
    position: absolute;
    left: 0; width: 100%; bottom: 0;
    background: var(--band-black);
  }
  .card--front .band-orange { top: 250px; height: 26px; }
  .card--front .band-black { top: 276px; }

  /* Back */
  .back-logo {
    position: absolute;
    left: 150px; top: 54px;
    font-family: "Josefin Sans", sans-serif;
    font-weight: 300;
    font-size: 38px;
    line-height: 1;
    letter-spacing: 11px;
    text-transform: uppercase;
    color: var(--ink);
    white-space: nowrap;
  }
  .back-person {
    position: absolute;
    left: 70px; top: 172px;
    font-weight: 700;
    font-size: 27px;
    color: #3a3a3a;
    white-space: nowrap;
  }
  .back-divider {
    position: absolute;
    left: 370px; top: 130px;
    width: 1.5px; height: 118px;
    background: var(--ink);
  }
  .contact-list {
    position: absolute;
    left: 392px; top: 140px;
    list-style: none;
    font-size: 17px;
    line-height: 27px;
    color: var(--ink);
    white-space: nowrap;
  }
  .contact-list li { display: flex; align-items: center; gap: 8px; }
  .icon {
    width: 15px; height: 15px;
    background: var(--ink);
    border-radius: 2px;
    display: inline-flex; align-items: center; justify-content: center;
    flex: none;
  }
  .card--back .band-orange { top: 268px; height: 20px; }
  .card--back .band-black { top: 288px; }
  .social {
    position: absolute;
    top: 332px;
    display: flex; align-items: center; gap: 10px;
    font-size: 16px;
    color: var(--text-light);
    white-space: nowrap;
  }
  .social--instagram { left: 40px; }
  .social--facebook { left: 300px; }
  .social-mark {
    width: 14px; height: 14px;
    background: #bdbdbd;
    border-radius: 2px;
    flex: none;
  }
</style>
</head>
<body>
  <section class="card card--front">
    <div class="front-photo" role="img" aria-label="Soft watercolour-toned fashion photograph in grey, violet and teal"></div>
    <div class="front-name">Marlow Thread</div>
    <div class="band-orange"></div>
    <div class="band-black"></div>
  </section>

  <section class="card card--back">
    <div class="back-logo">Marlow Thread</div>
    <div class="back-person">Karen Whitfield</div>
    <div class="back-divider"></div>
    <ul class="contact-list">
      <li>
        <span class="icon"><svg width="11" height="11" viewBox="0 0 24 24"><path fill="#fff" d="M6.6 10.8a15.1 15.1 0 0 0 6.6 6.6l2.2-2.2c.3-.3.7-.4 1-.2 1.1.4 2.3.6 3.6.6.6 0 1 .4 1 1V20c0 .6-.4 1-1 1A17 17 0 0 1 3 4c0-.6.4-1 1-1h3.5c.6 0 1 .4 1 1 0 1.3.2 2.5.6 3.6.1.3 0 .7-.2 1z"/></svg></span>
        0498716204
      </li>
      <li>
        <span class="icon"><svg width="11" height="11" viewBox="0 0 24 24"><rect x="2" y="5" width="20" height="14" fill="#fff"/><path d="M2 5l10 8 10-8" fill="none" stroke="#2b2b2b" stroke-width="2"/></svg></span>
        info@marlowthread.example.au
      </li>
      <li>
        <span class="icon"><svg width="11" height="11" viewBox="0 0 24 24"><circle cx="12" cy="12" r="9" fill="none" stroke="#fff" stroke-width="2.5"/><path d="M3 12h18M12 3c3 3 3 15 0 18M12 3c-3 3-3 15 0 18" fill="none" stroke="#fff" stroke-width="2"/></svg></span>
        www.marlowthread.example.au
      </li>
    </ul>
    <div class="band-orange"></div>
    <div class="band-black"></div>
    <div class="social social--instagram"><span class="social-mark"></span>marlow_thread</div>
    <div class="social social--facebook"><span class="social-mark"></span>www.fakebookexample.com/marlowthreadau/</div>
  </section>
</body>
</html>
```